Maritime Law Firm Business Card Design Project

We are a new maritime law firm starting in Queensland, Australia. The principal is a master mariner as well as a lawyer and is looking for a logo design that evokes a practical and user-friendly approach to the law, as well as maritime law expertise.

We would like to use the compass rose as the foundation for the design, as it symbolises clarity of direction and purpose, as well as traditional maritime heritage.

The 16th Century Luis Terradell Compass Rose (attached) is beautiful, but is too complex for a logo. A simplified version is desired.

Colour Paletter s flexible, although a B&W version is also needed. Colour suggestions are navy blue (for the sea), red and green (navigation lights) and maroon (for Queensland).

Target Market(s)

Maritime Industry/legal services

Industry/Entity Type

Law Firm

Font styles to use
Sans Serif

Requirements
Must have
• Contact Details
Name of 'Pellicott Legal'

```html
<!DOCTYPE html>
<html lang="en">
<head>
<meta charset="utf-8">
<title>Pellicott Legal – Business Card</title>
<link rel="stylesheet" href="https://fonts.googleapis.com/css2?family=Open+Sans:wght@400;600;700&display=swap">
<style>
  :root {
    --backdrop: #3b1214;
    --card: #ffffff;
    --navy: #16244f;
    --navy-band: #0e1a33;
    --red: #e0262c;
    --green: #1f8a3c;
    --muted: #2c3550;
  }
  * { box-sizing: border-box; margin: 0; padding: 0; }
  html, body {
    width: 1200px; height: 800px; overflow: hidden;
    background: var(--backdrop);
    font-family: "Open Sans", sans-serif;
  }
  .stage {
    width: 1200px; height: 800px;
    display: flex; align-items: center; justify-content: center;
  }
  .business-card {
    position: relative;
    width: 900px; height: 514px;
    background: var(--card);
    overflow: hidden;
    box-shadow: 0 20px 40px rgba(0,0,0,.45);
  }
  .brand {
    position: absolute; left: 56px; top: 56px;
    display: flex; align-items: center; gap: 22px;
  }
  .brand-mark {
    width: 140px; height: 140px; border-radius: 50%;
    background: var(--navy);
    flex: none;
  }
  .brand-name {
    font-size: 56px; font-weight: 600; color: var(--navy);
    letter-spacing: .5px; line-height: 1;
    margin-top: -50px;
  }
  .person { position: absolute; left: 60px; top: 244px; }
  .person-name {
    font-size: 30px; font-weight: 700; color: var(--red);
    letter-spacing: .5px; line-height: 1.1;
  }
  .person-role { font-size: 17px; color: var(--muted); margin-top: 2px; }
  .contact-list {
    list-style: none; position: absolute; left: 60px; top: 318px;
  }
  .contact-item {
    display: flex; align-items: center; gap: 14px;
    font-size: 22px; color: var(--navy); line-height: 31px;
  }
  .contact-icon { width: 18px; height: 18px; fill: var(--red); flex: none; }
  .accent-stripe {
    position: absolute; left: 0; right: 0; bottom: 46px; height: 6px;
    background: var(--green);
  }
  .bottom-band {
    position: absolute; left: 0; right: 0; bottom: 0; height: 46px;
    background: var(--navy-band);
  }
</style>
</head>
<body>
<main class="stage">
  <article class="business-card">
    <div class="brand">
      <div class="brand-mark"></div>
      <div class="brand-name">Pellicott Legal</div>
    </div>

    <div class="person">
      <div class="person-name">DANA WHITLOW</div>
      <div class="person-role">Manager</div>
    </div>

    <ul class="contact-list">
      <li class="contact-item">
        <svg class="contact-icon" viewBox="0 0 24 24"><path d="M6.6 10.8a15 15 0 0 0 6.6 6.6l2.2-2.2a1 1 0 0 1 1-.25 11.4 11.4 0 0 0 3.6.57 1 1 0 0 1 1 1V20a1 1 0 0 1-1 1A17 17 0 0 1 3 4a1 1 0 0 1 1-1h3.5a1 1 0 0 1 1 1c0 1.25.2 2.45.57 3.57a1 1 0 0 1-.25 1z"/></svg>
        0400 182 736
      </li>
      <li class="contact-item">
        <svg class="contact-icon" viewBox="0 0 24 24"><path d="M7 2h10a2 2 0 0 1 2 2v16a2 2 0 0 1-2 2H7a2 2 0 0 1-2-2V4a2 2 0 0 1 2-2zm0 3v11h10V5zm5 13.2a1.2 1.2 0 1 0 0 2.4 1.2 1.2 0 0 0 0-2.4z"/></svg>
        0400 594 218
      </li>
      <li class="contact-item">
        <svg class="contact-icon" viewBox="0 0 24 24"><path d="M3 5h18a1 1 0 0 1 1 1v12a1 1 0 0 1-1 1H3a1 1 0 0 1-1-1V6a1 1 0 0 1 1-1zm1 2.3V17h16V7.3l-8 5.2z M4.8 7 12 11.7 19.2 7z"/></svg>
        info@pellicottlegal.com
      </li>
      <li class="contact-item">
        <svg class="contact-icon" viewBox="0 0 24 24"><path d="M12 3 2 12h3v8h5v-5h4v5h5v-8h3z"/></svg>
        po box, harbour street, Queensland
      </li>
    </ul>

    <div class="accent-stripe"></div>
    <div class="bottom-band"></div>
  </article>
</main>
</body>
</html>
```